Quillmarsh Property Solutions need a business card design

Hello guys. We would need a business card design asap please.
We are a start up property investment business based in London UK specialised in buying, selling, managing and letting properties and helping distressed property owners.
The name of our Business is Quillmarsh, the logo symbolises the four fundamental elements of the world (earth, air, fire and water) and so it stands for strength, stability, longevity.
We would like the business card to communicate professionalism and reliability. Many many thanks indeed for your work.

Details:

1.) Rosalind Updike
Property Investor
Mobile: +44(0)7700123456
Email: rosalind.quillmarsh@mailbox-example.com

2.) Dominic Updike
Property Investor
Mobile: +44(0)7700987654
Email: dominic.quillmarsh@mailbox-example.com

```html
<!DOCTYPE html>
<html lang="en">
<head>
<meta charset="utf-8">
<title>Quillmarsh Property Solutions – Business Card</title>
<link rel="stylesheet" href="https://fonts.googleapis.com/css2?family=Josefin+Sans:wght@600;700&family=Open+Sans:wght@400;600&display=swap">
<style>
  :root {
    --stage: #e9e9ee;
    --card-white: #ffffff;
    --brand-red: #bc2a36;
    --ink: #1d1d1f;
    --ink-soft: #4a4a4f;
    --accent-blue: #3a5fae;
    --rule: #b9b9be;
  }
  html, body {
    margin: 0;
    padding: 0;
    width: 1200px;
    height: 987px;
    overflow: hidden;
    background: var(--stage);
  }
  .canvas {
    width: 1200px;
    height: 987px;
    display: flex;
    flex-direction: column;
    align-items: center;
    justify-content: center;
    gap: 30px;
  }
  .card {
    position: relative;
    width: 800px;
    height: 457px;
    border-radius: 36px;
    box-sizing: border-box;
    overflow: hidden;
    box-shadow: 0 2px 6px rgba(0,0,0,0.12);
  }
  /* Front */
  .card--front { background: var(--card-white); }
  .brand {
    position: absolute;
    left: 70px;
    top: 70px;
    display: flex;
    align-items: center;
    gap: 16px;
    font-family: "Josefin Sans", sans-serif;
    font-weight: 700;
    color: var(--ink);
  }
  .brand__mark {
    width: 22px;
    height: 22px;
    background: var(--brand-red);
  }
  .brand__name {
    line-height: 1;
    letter-spacing: 0.5px;
  }
  .brand__name-main { display: block; font-size: 36px; text-transform: uppercase; }
  .brand__name-sub { display: block; font-size: 14px; text-transform: uppercase; margin-top: 6px; letter-spacing: 1px; }
  .divider {
    position: absolute;
    left: 0;
    right: 0;
    top: 212px;
    height: 2px;
    background: linear-gradient(90deg, rgba(185,185,190,0) 0%, var(--rule) 25%, var(--rule) 100%);
  }
  .contacts {
    position: absolute;
    left: 70px;
    top: 245px;
    margin: 0;
    padding: 0;
    list-style: none;
    font-family: "Open Sans", sans-serif;
    font-size: 20px;
    color: var(--ink-soft);
  }
  .contacts__item {
    display: flex;
    align-items: center;
    gap: 12px;
    margin-bottom: 14px;
  }
  .contacts__icon { width: 16px; height: 16px; flex: none; }
  .person {
    position: absolute;
    right: 70px;
    bottom: 52px;
    text-align: left;
    font-family: "Open Sans", sans-serif;
  }
  .person__name {
    margin: 0;
    font-size: 27px;
    font-weight: 600;
    color: var(--brand-red);
  }
  .person__role {
    margin: 0;
    font-size: 21px;
    color: var(--accent-blue);
  }
  /* Back */
  .card--back {
    background: var(--brand-red);
    display: flex;
    align-items: center;
    justify-content: center;
  }
  .back-brand {
    font-family: "Josefin Sans", sans-serif;
    font-weight: 700;
    color: #ffffff;
    text-transform: uppercase;
    line-height: 1;
  }
  .back-brand__main { display: block; font-size: 66px; letter-spacing: 2px; }
  .back-brand__sub { display: block; font-size: 28px; letter-spacing: 2px; margin-top: 12px; }
</style>
</head>
<body>
<main class="canvas">
  <section class="card card--front" aria-label="Business card front">
    <div class="brand">
      <span class="brand__mark" aria-hidden="true"></span>
      <span class="brand__name">
        <span class="brand__name-main">Quillmarsh</span>
        <span class="brand__name-sub">Property Solutions</span>
      </span>
    </div>
    <div class="divider" aria-hidden="true"></div>
    <ul class="contacts">
      <li class="contacts__item">
        <svg class="contacts__icon" viewBox="0 0 16 16" aria-hidden="true">
          <rect x="4" y="1" width="8" height="14" rx="1.5" fill="var(--accent-blue)"/>
          <rect x="5.5" y="3" width="5" height="6" fill="#fff"/>
          <circle cx="8" cy="12.3" r="1" fill="#fff"/>
        </svg>
        <span>+44(0)7700987654</span>
      </li>
      <li class="contacts__item">
        <svg class="contacts__icon" viewBox="0 0 16 16" aria-hidden="true">
          <circle cx="8" cy="8" r="8" fill="var(--accent-blue)"/>
          <rect x="3.5" y="5" width="9" height="6" fill="#fff"/>
          <path d="M3.5 5 L8 8.5 L12.5 5" fill="none" stroke="var(--accent-blue)" stroke-width="1"/>
        </svg>
        <span>dominic.quillmarsh@mailbox-example.com</span>
      </li>
    </ul>
    <div class="person">
      <p class="person__name">Dominic Updike</p>
      <p class="person__role">Property Investor</p>
    </div>
  </section>

  <section class="card card--back" aria-label="Business card back">
    <div class="back-brand">
      <span class="back-brand__main">Quillmarsh</span>
      <span class="back-brand__sub">Property Solutions</span>
    </div>
  </section>
</main>
</body>
</html>
```